Facebook template for supermarket

I need a new fresh Facebook template in which I can paste an image that changes depending on the content of the Facebook post. I need to be able to change the design in Adobe Photoshop. It concerns the FB page of a local supermarket.
I once made a template myself, but I'm not satisfied with it.
Check the supermarket's website to see the supermarket's color scheme and style. The supermarket is a forerunner in the field of fresh products from local suppliers and has a wide range of organic products.
The slogan of the supermarket is 'With VELDO you find fine meals, your street and true friends'. The supermarket has a strong bond with the neighborhood and the inhabitants.
I have added my self-made template as an example. At the bottom right is the name of the owners of the supermarket.

```html
<!DOCTYPE html>
<html lang="en">
<head>
<meta charset="utf-8">
<title>VELDO Facebook post</title>
<link rel="stylesheet" href="https://fonts.googleapis.com/css2?family=Poppins:wght@400;600;700&display=swap">
<style>
  :root {
    --brand-green: #66b21d;
    --brand-green-light: #8cc83a;
    --brand-green-text: #6ab023;
    --white: #ffffff;
    --produce-orange: #f0922a;
    --produce-red: #b3263a;
    --produce-pink: #e56a97;
    --produce-shade: #c96a2a;
  }
  html, body {
    margin: 0;
    padding: 0;
    overflow: hidden;
  }
  body {
    width: 1200px;
    height: 1200px;
    background: var(--white);
  }
  .post {
    position: relative;
    width: 1200px;
    height: 1200px;
    background: var(--brand-green);
    font-family: "Poppins", Arial, sans-serif;
    overflow: hidden;
  }
  .post__shapes {
    position: absolute;
    inset: 0;
    width: 1200px;
    height: 1200px;
  }
  .post__headline {
    position: absolute;
    top: 52px;
    left: 0;
    width: 1200px;
    margin: 0;
    text-align: center;
    color: var(--white);
    font-weight: 600;
    font-size: 47px;
    line-height: 64px;
  }
  .post__slogan {
    position: absolute;
    left: 63px;
    top: 1058px;
    margin: 0;
    color: var(--white);
    font-weight: 400;
    font-size: 25px;
    line-height: 42px;
  }
  .post__slogan strong {
    font-weight: 700;
  }
  .sign {
    position: absolute;
    left: 690px;
    top: 1040px;
    width: 480px;
    text-align: center;
    color: var(--brand-green-text);
  }
  .sign__name {
    margin: 0;
    font-weight: 700;
    font-size: 46px;
    line-height: 56px;
  }
  .sign__owners {
    margin: 8px 0 0;
    font-weight: 700;
    font-size: 25px;
    line-height: 32px;
  }
</style>
</head>
<body>
  <main class="post">
    <svg class="post__shapes" viewBox="0 0 1200 1200" xmlns="http://www.w3.org/2000/svg">
      <defs>
        <linearGradient id="produce-tones" x1="0" y1="0" x2="1" y2="0">
          <stop offset="0" stop-color="var(--produce-pink)"/>
          <stop offset="0.18" stop-color="var(--produce-orange)"/>
          <stop offset="0.45" stop-color="var(--produce-red)"/>
          <stop offset="0.7" stop-color="var(--produce-orange)"/>
          <stop offset="1" stop-color="var(--produce-pink)"/>
        </linearGradient>
      </defs>
      <path class="arch-band" d="M0 285 Q560 150 1200 285 L1200 305 Q560 175 0 305 Z" fill="var(--brand-green-light)"/>
      <path class="photo-slot" role="img" aria-label="Photo of supermarket shelves stocked with oranges, red apples and pink-netted apples"
            d="M0 305 Q560 175 1200 305 L1200 1012 L0 1012 Z" fill="url(#produce-tones)"/>
      <polygon class="sign-panel" points="705,942 1200,942 1200,1200 570,1200" fill="var(--white)"/>
    </svg>

    <h1 class="post__headline">Lorem ipsum dolor nibh diam sit amet<br>consectetur adipiscing elit</h1>

    <p class="post__slogan">With <strong>VELDO</strong> you find <strong>fine meals</strong>,<br>your street and true friends</p>

    <div class="sign">
      <p class="sign__name">Wij zijn VELDO</p>
      <p class="sign__owners">VELDO Bram en Lotte de Vries</p>
    </div>
  </main>
</body>
</html>
```